Quorva - corporate Business Card

We need a good look and innovative business card for a new start up company based in Los Angeles called "Quorva". We are in a payment business, including payment card, app, and ewallet. We are expert in online payment and Card not present (CNP) transaction.
We need an innovative, modern business card.

Our logo font is Aero Matics

Target Market(s)

Startup - Bank - Online Payment - Card Manufacturing

Industry/Entity Type

Startup

Contact Information for Business Card

phone: 555 014 7396 - Address: 4172 Marlowe blvd, Halden City, NV 89299

Requirements
Must have
• Message: innovative, professional, expert, high tech, trust, online payment expert, security
Nice to have
• no comment
Should not have
• no Comment

```html
<!DOCTYPE html>
<html lang="en">
<head>
<meta charset="utf-8">
<title>Quorva – Business Card</title>
<link rel="stylesheet" href="https://fonts.googleapis.com/css2?family=Open+Sans:wght@400;600;700&family=Roboto:wght@900&display=swap">
<style>
  :root {
    --brand-red: #b81f2e;
    --brand-red-soft: #c0303d;
    --card-white: #f2f2f2;
    --ink: #2b2b2b;
    --backdrop-top: #c6c6c6;
    --backdrop-bottom: #a9a9a9;
    --white: #ffffff;
  }
  * { margin: 0; padding: 0; box-sizing: border-box; }
  html, body { width: 1200px; height: 900px; overflow: hidden; }
  body {
    position: relative;
    background: linear-gradient(to bottom, var(--backdrop-top), var(--backdrop-bottom));
    font-family: "Open Sans", Arial, sans-serif;
  }
  .card {
    position: absolute;
    top: 170px;
    width: 347px;
    height: 561px;
    overflow: hidden;
    text-align: center;
  }
  .card--front { left: 259px; background: var(--card-white); }
  .card--back { left: 631px; background: var(--brand-red); }

  .brand-dot {
    position: absolute;
    left: 103px; top: 52px;
    width: 140px; height: 140px;
    border-radius: 50%;
    background: var(--brand-red);
  }
  .wordmark {
    position: absolute;
    left: 0; right: 0; top: 212px;
    font-size: 66px;
    font-weight: 600;
    letter-spacing: 2px;
    color: var(--brand-red);
    line-height: 1;
  }
  .holder-name {
    position: absolute;
    left: 0; right: 0; top: 367px;
    font-family: "Roboto", Arial, sans-serif;
    font-weight: 900;
    font-size: 20px;
    letter-spacing: 0.5px;
    color: var(--brand-red);
  }
  .holder-title {
    position: absolute;
    left: 0; right: 0; top: 389px;
    font-size: 14.5px;
    color: var(--ink);
  }
  .contact {
    position: absolute;
    left: 0; right: 0; top: 429px;
    font-size: 14px;
    line-height: 21px;
    color: var(--ink);
  }
  .contact .website { color: var(--brand-red); font-weight: 700; }
  .contact .address { margin-top: 10px; }

  .back-halo {
    position: absolute;
    left: -30px; top: 50px;
    width: 410px; height: 410px;
    border-radius: 50%;
    background: var(--brand-red-soft);
    opacity: 0.55;
  }
  .back-badge {
    position: absolute;
    left: 78px; top: 120px;
    width: 180px; height: 180px;
    border-radius: 50%;
    background: var(--white);
    display: flex;
    align-items: center;
    justify-content: center;
    font-size: 34px;
    font-weight: 600;
    color: var(--brand-red);
  }
  .values {
    position: absolute;
    left: 0; right: 0; top: 428px;
    list-style: none;
    color: var(--white);
    font-size: 15px;
    line-height: 29.5px;
    text-transform: uppercase;
  }
  .values li { white-space: nowrap; }
  .value { margin: 0 2px; }
  .value::before {
    content: "";
    display: inline-block;
    width: 7px; height: 7px;
    margin-right: 3px;
    border-radius: 50%;
    background: var(--white);
    vertical-align: 2px;
  }
</style>
</head>
<body>
  <section class="card card--front" aria-label="Business card front">
    <div class="brand-dot"></div>
    <div class="wordmark">quorva</div>
    <div class="holder-name">DANIEL BROOKS</div>
    <div class="holder-title">Managing Director</div>
    <div class="contact">
      <div class="phone">555 014 7396</div>
      <div class="website">www.quorva.com</div>
      <div class="address">4172 Marlowe blvd,<br>Halden City, NV 89299</div>
    </div>
  </section>

  <section class="card card--back" aria-label="Business card back">
    <div class="back-halo"></div>
    <div class="back-badge">quorva</div>
    <ul class="values">
      <li><span class="value">Innovative</span> <span class="value">Professional</span></li>
      <li><span class="value">Expert</span><span class="value">High Tech</span><span class="value">Trust</span></li>
      <li><span class="value">Online Payment Expert</span><span class="value">Security</span></li>
    </ul>
  </section>
</body>
</html>
```